Velvet Meadow Hamper company needs a brochure design

We need a brochure design for a new company in Dubai called 'Velvet Meadow Hampers'. We already have a logo designed which I have attached and would like to use this and the green/gold/white colours for our brochure. Our company initially will be supplying Velvet Meadow Hamper wear of traditional wicker baskets in many designs which hold all the cutlery, crockery and accessories. We will also be selling picnic accessories. We want to purvey a sense of luxury and class in line with our logo. I have attached some photos of the picnicwear. As our products are changing all the time I thought a fold out cover which stays the same and then product cards inserted into the folder which can be changed according to our product changes. I am looking for a fairly simple design and each product card should have at least one photo of the product on it with a spec and description also. On the cover of the folder I would like room to write about the company and what we do, this can be inside or out and may or may not include photos. I have the logo designs in illustrator format and pdf. Please contact if any more information is needed.
Updates

Reason: I have extended this deadline as there are some content changes taking place.

Industry/Entity Type

It Company

```html
<!DOCTYPE html>
<html lang="en">
<head>
<meta charset="utf-8">
<title>Velvet Meadow Hampers – Product Card</title>
<link rel="stylesheet" href="https://fonts.googleapis.com/css2?family=Arimo:wght@400;700&family=Gelasio:wght@400&display=swap">
<style>
  :root {
    --forest: #1b3119;
    --forest-deep: #172b16;
    --gold: #c9a23c;
    --gold-soft: #b8943a;
    --ivory: #f4f1e8;
    --paper: #ffffff;
    --bronze: #6e2a18;
    --wicker: #9c8560;
    --wicker-light: #d9ceb2;
  }
  * { margin: 0; padding: 0; box-sizing: border-box; }
  html, body { width: 1200px; height: 1000px; overflow: hidden; background: var(--paper); }
  body { position: relative; font-family: "Gelasio", Georgia, serif; }

  .card { position: absolute; top: 150px; width: 493px; height: 700px; background: var(--forest); overflow: hidden; }
  .card--front { left: 100px; }
  .card--spec { left: 607px; }

  .brand-band { position: absolute; top: 0; left: 0; width: 100%; height: 147px; display: flex; align-items: center; justify-content: center; padding-top: 4px; }
  .brand-name { font-family: "Arimo", Arial, sans-serif; font-weight: 700; font-size: 12.5px; letter-spacing: 2.6px; color: var(--gold); text-transform: uppercase; }

  .metal-rule { position: absolute; left: 0; width: 100%; height: 6px;
    background: linear-gradient(90deg, var(--bronze) 0%, #a8682a 35%, #f7efd9 55%, #d2a33a 72%, var(--bronze) 100%); }
  .metal-rule--top { top: 147px; }
  .metal-rule--bottom { top: 513px; height: 7px; }

  .product-stage { position: absolute; top: 153px; left: 0; width: 100%; height: 360px; background: var(--paper); }
  .product-photo { position: absolute; left: 110px; top: 37px; width: 272px; height: 303px; border-radius: 6px;
    background: linear-gradient(180deg, var(--wicker) 0%, var(--wicker-light) 40%, var(--wicker) 75%, #8a7450 100%); }

  .front-copy { position: absolute; top: 536px; left: 28px; right: 40px; }
  .product-title { font-family: "Arimo", Arial, sans-serif; font-weight: 700; font-size: 24px; letter-spacing: 2.2px; color: var(--gold); line-height: 1; }
  .product-blurb { margin-top: 11px; font-size: 10.6px; line-height: 13.3px; color: var(--ivory); }

  .site-link { position: absolute; bottom: 14px; left: 0; width: 100%; text-align: center; font-size: 10.5px; color: var(--gold); }

  .spec-block { position: absolute; top: 193px; left: 0; width: 100%; }
  .flourish { display: block; margin: 0 auto; }
  .spec-title { margin-top: 24px; text-align: center; font-family: "Arimo", Arial, sans-serif; font-weight: 700; font-size: 23px; letter-spacing: 2.6px; color: var(--gold); line-height: 1; }
  .spec-subtitle { text-align: center; font-size: 15px; letter-spacing: 0.5px; color: var(--gold); margin-top: 5px; }
  .spec-list { list-style: none; margin: 22px 0 0 111px; }
  .spec-list li { position: relative; padding-left: 15px; font-size: 10.6px; line-height: 16.5px; color: var(--ivory); }
  .spec-list li::before { content: ""; position: absolute; left: 0; top: 6px; width: 6px; height: 5px; background: var(--gold-soft); }
  .spec-list li.continued::before { display: none; }
  .flourish--foot { margin-top: 18px; }
</style>
</head>
<body>

<section class="card card--front">
  <header class="brand-band">
    <span class="brand-name">Velvet Meadow Hampers</span>
  </header>
  <div class="metal-rule metal-rule--top"></div>
  <div class="product-stage">
    <div class="product-photo" role="img" aria-label="Photo of the open willow picnic basket for two, with cream leather straps, plates and cutlery fitted in the lid"></div>
  </div>
  <div class="metal-rule metal-rule--bottom"></div>
  <div class="front-copy">
    <h1 class="product-title">WILLOWBY, 2 Person</h1>
    <p class="product-blurb">This trendy picnic basket has been hand woven to the highest standards in antique wash willow and comes equipped for two people. The cream leather handles and trim gives a beautiful finish, while the integral chiller compartment means that your food and drink will remain ready to consume. This basket is perfect for those romantic picnics for two on a sunny afternoon and would make a great wedding or anniversary gift for a happy couple.</p>
  </div>
  <p class="site-link">www.velvetmeadowhampers.com</p>
</section>

<section class="card card--spec">
  <div class="spec-block">
    <svg class="flourish" width="134" height="20" viewBox="0 0 134 20" aria-hidden="true">
      <line x1="0" y1="18.5" x2="134" y2="18.5" stroke="var(--gold-soft)" stroke-width="1"/>
      <rect x="62" y="8" width="10" height="6" fill="var(--gold-soft)"/>
    </svg>
    <h2 class="spec-title">WILLOWBY, 2 Person</h2>
    <p class="spec-subtitle">OVERVIEW</p>
    <ul class="spec-list">
      <li>Handmade antique wash willow basket for two people</li>
      <li>Cream leather straps and trim</li>
      <li>Built in chiller compartment</li>
      <li>Contemporary cream and white colour palette</li>
      <li>2 White china plates</li>
      <li>2 Stainless steel, knifes, forks and spoons</li>
      <li>1 Stainless steel waiters friend bottle opener</li>
      <li>2 Wine glasses held in a willow basket,</li>
      <li class="continued">180 x 90 x 160mm</li>
      <li>Hamper dimensions, 400 x 300 x 200mm</li>
    </ul>
    <svg class="flourish flourish--foot" width="134" height="20" viewBox="0 0 134 20" aria-hidden="true">
      <line x1="0" y1="1.5" x2="134" y2="1.5" stroke="var(--gold-soft)" stroke-width="1"/>
      <rect x="62" y="7" width="10" height="6" fill="var(--gold-soft)"/>
    </svg>
  </div>
  <p class="site-link">www.velvetmeadowhampers.com</p>
</section>

</body>
</html>
```